Varnik Holdings — Business Card Design Brief
Overview
Design a double-sided business card for Varnik Holdings that highlights our two service arms: Varnik Communications (telecommunications) and Varnik Energy (business energy solutions). The card should feel smart and stand out when handed to clients.

Objectives
Showcase our areas of specialty clearly.
Reflect the overall Varnik / Varnik Holdings brand while acknowledging both arms.
Explore using both logos (Communications + Energy) or one unified logo, depending on the design.

Deliverables
One double-sided business card design (front + back).

Content & Copy
Front (preferred): Logo: Varnik / Varnik Holdings
Descriptor: Business Communications | Business Energy
Back:My contact details and company details
Core products: Business Mobile • Telephony • Internet • Business Energy Solutions

Brand & Visual Direction
We have a group logo currently tailored more toward telecoms, plus a separate Varnik Energy logo.
Please explore layouts that use both logos or just one, whichever works best.
Color: I wouldn't mind seeing an option using our the Blue/Purple gradient from our website (varnik-example.co.uk), but also open to non-gradient approaches and other colours..

Overall look: Smart, modern, and distinctive.
Format & Print Specs
Double-sided business card format. (Use a standard size

Must-Haves
Front: Varnik wording or Varnik Holdings wording with atleast 1 logo also on front “Business Communications | Business Energy.”

Back: Contact + company details and core products.
A design that stands out while remaining professional.

Nice-to-Have Options
A gradient version using our site’s Blue/Purple gradient.
A non-gradient version.
A dual-logo treatment versus a single-logo treatment.

Thanks
Owen

```html
<!DOCTYPE html>
<html lang="en">
<head>
<meta charset="utf-8">
<title>Varnik Holdings — Business Card</title>
<link rel="stylesheet" href="https://fonts.googleapis.com/css2?family=Montserrat:wght@400;500;600;800&display=swap">
<style>
  :root{
    --stage:#d9d9db;
    --white:#ffffff;
    --navy:#1f1b5e;
    --ink:#23214a;
    --sky:#1da1e0;
    --blue:#1f6fb8;
    --purple:#7a4a9e;
    --grad-end:#1565a6;
    --green:#6cbf3c;
    --divider:#9cc6ea;
  }
  *{box-sizing:border-box;margin:0;padding:0}
  html,body{width:1200px;height:802px;overflow:hidden}
  body{background:var(--stage);font-family:"Montserrat",sans-serif;position:relative}

  .card{position:absolute;top:246px;width:540px;height:309px;border-radius:18px;overflow:hidden;
        box-shadow:0 10px 24px rgba(0,0,0,.22)}
  .card--contact{left:40px;background:var(--white)}
  .card--brand{left:620px;background:linear-gradient(120deg,var(--purple) 0%,#5a58a0 45%,var(--grad-end) 100%)}

  /* shared brand lockup */
  .lockup{display:flex;align-items:center;gap:10px}
  .lockup__dot{width:34px;height:34px;border-radius:50%;flex:none}
  .lockup__name{font-weight:800;letter-spacing:.02em;line-height:1}

  /* contact side */
  .contact-lockup{position:absolute;left:34px;top:40px}
  .contact-lockup .lockup__dot{background:var(--sky)}
  .contact-lockup .lockup__name{font-size:40px;color:var(--navy)}

  .person{position:absolute;left:34px;top:162px}
  .person__name{font-size:22px;font-weight:800;color:var(--navy);letter-spacing:.02em}
  .person__role{font-size:13px;font-weight:500;color:var(--ink);margin-top:3px}

  .contact-divider{position:absolute;left:262px;top:44px;width:1px;height:178px;background:var(--divider)}

  .details{position:absolute;left:280px;top:52px;list-style:none;color:var(--ink);font-size:12.5px;line-height:1.45}
  .details__address{margin-bottom:10px}
  .details__row{display:flex;align-items:center;gap:8px}
  .details__icon{width:13px;height:13px;flex:none}

  .products{position:absolute;left:0;bottom:0;width:100%;height:34px;background:var(--navy);
            color:var(--white);font-size:12.5px;font-weight:500;display:flex;align-items:center;justify-content:center;gap:8px}
  .products__sep{color:var(--sky);font-weight:800}

  /* brand side */
  .arm{position:absolute;top:0;height:100%;width:50%;display:flex;flex-direction:column;justify-content:center;align-items:center;gap:26px}
  .arm--comms{left:0}
  .arm--energy{right:0}
  .arm .lockup__name{font-size:42px;color:var(--white)}
  .arm--comms .lockup__dot{background:var(--sky)}
  .arm--energy .lockup__dot{background:var(--green)}
  .arm__descriptor{font-size:14px;font-weight:600;color:var(--white);letter-spacing:.02em}
  .brand-divider{position:absolute;left:50%;top:70px;width:1px;height:170px;background:var(--green)}
</style>
</head>
<body>

<section class="card card--contact" aria-label="Contact side">
  <div class="lockup contact-lockup">
    <span class="lockup__dot"></span>
    <span class="lockup__name">VARNIK</span>
  </div>

  <div class="person">
    <p class="person__name">ADRIAN COLE</p>
    <p class="person__role">Founder/CEO</p>
  </div>

  <div class="contact-divider"></div>

  <ul class="details">
    <li class="details__address">24 Larkfield Road,<br>Leeds England, LS2 7QP</li>
    <li class="details__row">
      <svg class="details__icon" viewBox="0 0 16 16" aria-hidden="true"><path fill="#1da1e0" d="M3.5 1.5l2.5 0 1 3.5-1.6 1.2a8 8 0 0 0 4.4 4.4L11 9l3.5 1v2.5c0 1-1 2-2 2A11 11 0 0 1 1.5 3.5c0-1 1-2 2-2z"/></svg>
      +44 0113 496 0721
    </li>
    <li class="details__row">
      <svg class="details__icon" viewBox="0 0 16 16" aria-hidden="true"><rect x="1" y="3" width="14" height="10" rx="1.5" fill="#1da1e0"/><path d="M1.5 4l6.5 5 6.5-5" stroke="#fff" stroke-width="1.3" fill="none"/></svg>
      info@varnik-example.co.uk
    </li>
    <li class="details__row">
      <svg class="details__icon" viewBox="0 0 16 16" aria-hidden="true"><circle cx="8" cy="8" r="7" fill="#1da1e0"/><path d="M1 8h14M8 1c-3 3-3 11 0 14M8 1c3 3 3 11 0 14" stroke="#fff" stroke-width="1" fill="none"/></svg>
      www.varnik-example.co.uk
    </li>
  </ul>

  <p class="products">
    <span>Business Mobile</span><span class="products__sep">•</span>
    <span>Telephony</span><span class="products__sep">•</span>
    <span>Internet</span><span class="products__sep">•</span>
    <span>Business Energy Solutions</span>
  </p>
</section>

<section class="card card--brand" aria-label="Brand side">
  <div class="arm arm--comms">
    <div class="lockup">
      <span class="lockup__dot"></span>
      <span class="lockup__name">VARNIK</span>
    </div>
    <p class="arm__descriptor">Business Communications</p>
  </div>
  <div class="brand-divider"></div>
  <div class="arm arm--energy">
    <div class="lockup">
      <span class="lockup__dot"></span>
      <span class="lockup__name">VARNIK</span>
    </div>
    <p class="arm__descriptor">Business Energy</p>
  </div>
</section>

</body>
</html>
```